Craft beer label required for new modern craft brewery

I require a label to be designed for my craft beer, the name of the beer is "Lanternfish Pale Ale".
It has to be a contemporary style label targeting an audience group between the ages of 21-40. It must be unique and appealing.
The label must incorporate the image of a Gladiator which has to originally created (I’m giving you creative freedom), not copied (for copy right reasons). I’m attaching a few examples, please refer to “gladiator1.jpg” and “Gladiator2.jpg”.
It would be nice if the Coliseum could appear in the background, also originally created I’m attaching an example, please refer to “Coliseum1.jpg”
The Label must also incorporate the attached logo “Copperwell Brewing Co. Craft Beer-01.jpg” .
The label must fit a 440ml bottle
Please use creative freedom with regards to the shape of the label.
The colours do not have to be exactly the same as logo, but obviously they must match.
Updates

Project Deadline Extended Reason: Not 100% happy with the submissions, almost there.I'd also like to give those designers, that haven't submitted, a chance to submit. Added Tuesday, September 26, 2017

Target Market(s)

Modern/contemporary successful 21-40 year olds

Industry/Entity Type

Brewery

Font styles to use
Serif
Script

Colors

Designer to choose colors to be used in the design.

Requirements
Must have
• My logo, the beer name and the image of a gladiator
• The label size should be at least 10cm wide x 9cm wide.
• The label must include the size of the bottle: 440ml
• The label must include 6.5% ALC./VOL.
Nice to have
• Coliseum in the back ground
Should not have
• Copied images or trade marks

```html
<!DOCTYPE html>
<html lang="en">
<head>
<meta charset="utf-8">
<title>Lanternfish Pale Ale – Label</title>
<link rel="stylesheet" href="https://fonts.googleapis.com/css2?family=Alfa+Slab+One&family=Cinzel:wght@700&family=Kaushan+Script&family=Libre+Baskerville:wght@700&display=swap">
<style>
  :root {
    --page: #ecebe6;
    --ring: #141414;
    --ring-edge: #8c8c8c;
    --sky-light: #f3ead2;
    --sky-warm: #d9c7a0;
    --arena-stone: #b7a68a;
    --arena-shadow: #6e5a44;
    --sand: #c9b48e;
    --cream: #f1ebdc;
    --bronze-light: #d9a27a;
    --bronze: #a8704f;
    --outline: #2a1d16;
    --gold: #d8a642;
    --ink: #1b1b1b;
    --volume-text: #f4f4f4;
  }
  * { margin: 0; padding: 0; box-sizing: border-box; }
  html, body { width: 800px; height: 1200px; overflow: hidden; }
  body { background: var(--page); position: relative; }

  .label {
    position: absolute; left: 130px; top: 150px;
    width: 540px; height: 960px;
    border-radius: 50%;
    background: var(--ring);
    box-shadow: inset 0 0 0 3px var(--ring-edge);
  }
  .label-inner {
    position: absolute; inset: 26px;
    border-radius: 50%;
    overflow: hidden;
    background: var(--cream);
    box-shadow: 0 0 0 2px #3c3c3c;
  }
  .label-art {
    position: absolute; left: 0; top: 0; width: 100%; height: 68%;
    background:
      radial-gradient(ellipse at 50% 55%, rgba(90,60,40,.55) 0 18%, transparent 40%),
      linear-gradient(180deg, var(--sky-light) 0%, var(--sky-warm) 28%, var(--arena-stone) 50%, var(--arena-shadow) 72%, var(--sand) 100%);
  }
  .label-foot {
    position: absolute; left: 0; bottom: 0; width: 100%; height: 34%;
    background: linear-gradient(180deg, var(--sand) 0%, var(--cream) 30%, var(--cream) 60%, var(--ring) 64%, var(--ring) 100%);
  }

  .brand {
    position: absolute; left: 50%; top: 100px;
    transform: translateX(-50%);
    width: 210px; height: 210px;
    border-radius: 50%;
    background: var(--ring);
    box-shadow: 0 0 0 4px var(--gold);
    display: flex; align-items: center; justify-content: center;
    text-align: center;
  }
  .brand-name {
    font-family: "Cinzel", serif; font-weight: 700;
    font-size: 22px; line-height: 1.25; letter-spacing: 1px;
    color: var(--gold);
  }

  .beer-name {
    position: absolute; left: 50%; top: 694px;
    transform: translateX(-50%);
    font-family: "Alfa Slab One", serif;
    font-size: 70px; line-height: 1;
    color: var(--bronze);
    background: linear-gradient(180deg, var(--bronze-light), var(--bronze));
    -webkit-background-clip: text; background-clip: text;
    -webkit-text-fill-color: transparent;
    -webkit-text-stroke: 3px var(--outline);
    white-space: nowrap;
  }
  .beer-style {
    position: absolute; left: 0; right: 0; top: 790px;
    text-align: center;
    font-family: "Kaushan Script", cursive;
    font-size: 58px; line-height: 1;
    color: #f6f2ea;
    -webkit-text-stroke: 2px var(--ink);
  }
  .abv {
    position: absolute; left: 0; right: 0; top: 872px;
    text-align: center;
    font-family: "Libre Baskerville", serif; font-weight: 700;
    font-size: 18px; line-height: 1; color: var(--ink);
  }
  .volume {
    position: absolute; left: 0; right: 0; top: 1012px;
    text-align: center;
    font-family: "Libre Baskerville", serif; font-weight: 700;
    font-size: 30px; line-height: 1; color: var(--volume-text);
  }
</style>
</head>
<body>
  <div class="label">
    <div class="label-inner">
      <div class="label-art" role="img" aria-label="Illustration of a helmeted gladiator holding a sword, standing in the sandy arena of the Colosseum"></div>
      <div class="label-foot"></div>
    </div>
  </div>

  <div class="brand">
    <span class="brand-name">Copperwell<br>Brewing Co.</span>
  </div>

  <div class="beer-name">Lanternfish</div>
  <div class="beer-style">Pale Ale</div>
  <div class="abv">6,5% ALC/VOL</div>
  <div class="volume">440 ml</div>
</body>
</html>
```